Whitcombe Business Card Design

The name of the business is Dario Whitcombe, CPA LLC
The service that we offer is Accounting, Tax & Consulting Services. I need it to have the following items:
Dario Whitcombe, Principal
Phone Number
Email Address
Physical Address

I have attached the company logo, one in black and one in white. Please provide a design in black background and the other in white background. Please include "Accounting, Tax & Consulting Services". I want the business card to be clean and very professional.

```html
<!DOCTYPE html>
<html lang="en">
<head>
<meta charset="utf-8">
<title>Dario Whitcombe, CPA LLC — Business Cards</title>
<link href="https://fonts.googleapis.com/css2?family=Montserrat:wght@500;600&family=Tenor+Sans&display=swap" rel="stylesheet">
<style>
  :root {
    --bg: #e7e5e2;
    --card-dark: #333537;
    --card-light: #fbfbfb;
    --ink: #2e3032;
    --grey: #8c8d8f;
    --grey-soft: #ededed;
    --red: #8e1a1f;
    --white: #ffffff;
  }
  * { margin: 0; padding: 0; box-sizing: border-box; }
  html, body { width: 1200px; height: 900px; overflow: hidden; background: var(--bg); }
  .canvas { position: relative; width: 1200px; height: 900px; }

  .card {
    position: absolute; left: 250px; width: 700px; height: 400px;
    border-radius: 36px; overflow: hidden;
  }
  .card--front { top: 30px; background: var(--card-dark); }
  .card--back { top: 470px; background: var(--card-light); box-shadow: 0 2px 8px rgba(0,0,0,.12); }

  .brand { display: flex; align-items: center; gap: 16px; }
  .brand__square { flex: none; border: 5px solid currentColor; }
  .brand__name {
    font-family: "Montserrat", sans-serif; font-weight: 600;
    text-transform: uppercase; letter-spacing: .02em; line-height: 1;
  }
  .brand__tagline {
    font-family: "Montserrat", sans-serif; font-weight: 600;
    text-transform: uppercase; letter-spacing: .14em; color: var(--grey); margin-top: 8px;
  }
  .brand__services {
    font-family: "Tenor Sans", sans-serif; letter-spacing: .04em; color: var(--grey); margin-top: 8px;
  }

  .card--front .brand {
    position: absolute; left: 0; right: 0; top: 118px;
    flex-direction: column; gap: 22px; color: var(--white);
  }
  .card--front .brand__square { width: 90px; height: 64px; }
  .card--front .brand__text { text-align: center; }
  .card--front .brand__name { font-size: 34px; }
  .card--front .brand__tagline { font-size: 19px; }
  .card--front .brand__services { font-size: 16px; margin-top: 12px; color: #b9babc; }

  .card--back .brand { position: absolute; left: 36px; top: 46px; color: var(--ink); }
  .card--back .brand__square { width: 54px; height: 42px; }
  .card--back .brand__name { font-size: 25px; }
  .card--back .brand__tagline { font-size: 14px; margin-top: 6px; }
  .card--back .brand__services { font-size: 13px; margin-top: 5px; }

  .watermark-block {
    position: absolute; left: 40px; top: 160px; width: 300px; height: 280px;
    background: var(--grey-soft); opacity: .8;
  }

  .person { position: absolute; right: 290px; top: 232px; text-align: right; }
  .person__role { font-family: "Tenor Sans", sans-serif; font-size: 18px; color: var(--ink); }
  .person__name { font-family: "Tenor Sans", sans-serif; font-size: 21px; color: var(--red); margin-top: 4px; white-space: nowrap; }

  .divider { position: absolute; left: 424px; top: 212px; width: 1px; height: 126px; background: var(--grey); }

  .contact { position: absolute; left: 440px; top: 218px; list-style: none;
    font-family: "Tenor Sans", sans-serif; font-size: 15px; color: var(--ink); line-height: 1.4; }
  .contact li { display: flex; gap: 10px; margin-bottom: 9px; white-space: nowrap; }
  .contact svg { flex: none; width: 15px; height: 15px; margin-top: 2px; fill: var(--red); }
</style>
</head>
<body>
<main class="canvas">

  <section class="card card--front" aria-label="Business card front">
    <div class="brand">
      <span class="brand__square"></span>
      <div class="brand__text">
        <p class="brand__name">Dario Whitcombe, CPA, LLC</p>
        <p class="brand__tagline">Certified Public Accountant</p>
        <p class="brand__services">Accounting, Tax &amp; Consulting Services</p>
      </div>
    </div>
  </section>

  <section class="card card--back" aria-label="Business card back">
    <div class="watermark-block"></div>
    <div class="brand">
      <span class="brand__square"></span>
      <div class="brand__text">
        <p class="brand__name">Dario Whitcombe, CPA, LLC</p>
        <p class="brand__tagline">Certified Public Accountant</p>
        <p class="brand__services">Accounting, Tax &amp; Consulting Services</p>
      </div>
    </div>

    <div class="person">
      <p class="person__role">Principal</p>
      <p class="person__name">DARIO WHITCOMBE</p>
    </div>

    <span class="divider"></span>

    <ul class="contact">
      <li>
        <svg viewBox="0 0 24 24" aria-hidden="true"><path d="M6.6 10.8a15 15 0 0 0 6.6 6.6l2.2-2.2a1 1 0 0 1 1-.25 11.4 11.4 0 0 0 3.6.57 1 1 0 0 1 1 1V20a1 1 0 0 1-1 1A17 17 0 0 1 3 4a1 1 0 0 1 1-1h3.5a1 1 0 0 1 1 1c0 1.25.2 2.45.57 3.57a1 1 0 0 1-.25 1z"/></svg>
        <span>(00) 0000 0000</span>
      </li>
      <li>
        <svg viewBox="0 0 24 24" aria-hidden="true"><path d="M2 5h20v14H2zm2 2v.5l8 5 8-5V7zm0 2.8V17h16V9.8l-8 5z"/></svg>
        <span>dario@whitcombecpa.com</span>
      </li>
      <li>
        <svg viewBox="0 0 24 24" aria-hidden="true"><path d="M12 2a7 7 0 0 0-7 7c0 5 7 13 7 13s7-8 7-13a7 7 0 0 0-7-7zm0 9.5A2.5 2.5 0 1 1 12 6.5a2.5 2.5 0 0 1 0 5z"/></svg>
        <span>11 dummy city, dummy place,<br>P.O Box 0000 Dummy Land</span>
      </li>
    </ul>
  </section>

</main>
</body>
</html>
```